We are a local Communty Pharmacy wishing to promote and market a specialised Pharmaceutical Service

We would like a design that is professional and enticing ( according to the brief In attached files)
We wish to Market Compounding Pharmacy as a specialist side of our business.
We have the expertise a purpose built preparation laboratory.
The main purpose is an Internet presence that entices prospective patients to contact or visit our physical store.

Target Market(s)

Patients Medicos and Veterinary clients

Industry/Entity Type

Pharmacy

Coding

Coded - Design and coding required

Number of Pages Required

1 page

Requirements
Must have
• Clear friendly image
Nice to have
• soft enticing feel
Should not have
• No crass loud unprofessional elements

```html
<!DOCTYPE html>
<html lang="en">
<head>
<meta charset="utf-8">
<title>Riverton Compounding</title>
<link href="https://fonts.googleapis.com/css2?family=Open+Sans:wght@400;600;700&display=swap" rel="stylesheet">
<style>
:root{
  --cyan:#4fc3dc;
  --cyan-dark:#2fa9c4;
  --pink:#f072a9;
  --orange:#f6a93b;
  --teal:#43c8bd;
  --ink:#3a3d42;
  --muted:#8a8f96;
  --line:#e4e7ea;
  --paper:#ffffff;
  --soft:#f4f6f8;
  --footer:#2e3034;
  --footer-deep:#232427;
  --footer-text:#b9bdc3;
}
*{box-sizing:border-box;margin:0;padding:0}
html,body{width:700px;height:1200px;overflow:hidden}
body{font-family:"Open Sans",Arial,sans-serif;color:var(--ink);background:var(--paper);position:relative}
.abs{position:absolute}

.site-header{left:0;top:0;width:700px;height:48px;background:var(--paper);border-bottom:1px solid var(--line)}
.brand{left:22px;top:16px}
.brand-name{font-size:13px;font-weight:600;color:var(--ink);letter-spacing:.5px}
.main-nav{right:22px;top:0;height:48px;display:flex;align-items:center}
.main-nav a{display:flex;align-items:center;height:48px;padding:0 13px;font-size:8px;font-weight:600;color:var(--ink);text-decoration:none;letter-spacing:.5px}
.main-nav a.active{background:var(--cyan);color:#fff}
.nav-search{margin-left:6px}

.hero{left:0;top:48px;width:700px;height:282px;background:linear-gradient(100deg,#e9eef1 0%,#f7f9fa 30%,#dfe8ec 55%,#c9d9df 75%,#e6eef1 100%)}
.hero-shade{left:380px;top:190px;width:300px;height:80px;background:linear-gradient(90deg,rgba(60,110,130,0) 0%,rgba(60,110,130,.35) 40%,rgba(60,110,130,.35) 100%)}
.hero-caption{left:440px;top:210px;width:240px;color:#fff}
.hero-caption h1{font-size:15px;font-weight:600;letter-spacing:.6px;margin-bottom:5px}
.hero-caption p{font-size:7px;line-height:1.5}
.hero-arrow{top:174px;width:20px;height:20px;border-radius:50%;background:rgba(255,255,255,.75);display:flex;align-items:center;justify-content:center}
.hero-dots{left:330px;top:316px;display:flex;gap:5px}
.hero-dots span{width:6px;height:6px;border-radius:50%;background:rgba(255,255,255,.7)}
.hero-dots span.on{background:var(--cyan)}

.tile{top:350px;width:193px;height:106px;padding:12px 10px;color:#fff;overflow:hidden}
.tile h2{font-size:10px;font-weight:700;letter-spacing:.4px;margin-bottom:6px;position:relative}
.tile p{font-size:6.5px;line-height:1.55;width:110px;position:relative}
.tile-art{right:0;top:0;width:95px;height:106px}
.tile-medicine{left:22px;background:var(--pink)}
.tile-medicine .tile-art{background:linear-gradient(90deg,rgba(240,114,169,0),rgba(255,200,225,.55))}
.tile-popular{left:253px;background:var(--orange)}
.tile-popular .tile-art{background:linear-gradient(90deg,rgba(246,169,59,0),rgba(255,225,180,.55))}
.tile-care{left:484px;background:var(--teal)}
.tile-care .tile-art{background:linear-gradient(90deg,rgba(67,200,189,0),rgba(190,240,235,.55))}

.section-title{font-size:11px;font-weight:700;letter-spacing:.4px;color:var(--ink)}
.section-title::after{content:"";display:block;width:28px;height:2px;background:var(--cyan);margin-top:5px}
.about{left:22px;top:478px;width:410px}
.about p,.works p{font-size:6.5px;line-height:1.65;color:var(--muted);margin-top:9px}
.btn-outline{display:inline-block;margin-top:12px;padding:5px 9px;font-size:6.5px;font-weight:600;color:#fff;background:var(--cyan);letter-spacing:.4px}
.works{left:460px;top:478px;width:218px}
.works ul{list-style:none;margin-top:8px}
.works li{display:flex;align-items:center;gap:6px;font-size:7px;color:var(--muted);padding:4px 0;border-bottom:1px solid var(--line)}

.question{left:0;top:672px;width:700px;height:76px;background:var(--cyan);color:#fff;padding:14px 22px}
.question h2{font-size:14px;font-weight:600;letter-spacing:.6px}
.question p{font-size:6.5px;line-height:1.6;width:430px;margin-top:5px}
.btn-quote{right:22px;top:26px;padding:7px 16px;border:1px solid #fff;font-size:8px;font-weight:600;letter-spacing:.5px}

.products{left:22px;top:766px;width:656px}
.product-arrows{right:22px;top:768px;display:flex;gap:4px}
.product-arrows span{width:14px;height:14px;border-radius:50%;border:1px solid var(--line);display:flex;align-items:center;justify-content:center}
.product{top:796px;width:152px}
.product-photo{width:152px;height:96px;border:1px solid var(--line);background:var(--soft)}
.product h3{font-size:7px;font-weight:600;color:var(--cyan-dark);margin-top:7px;letter-spacing:.3px}
.stars{display:flex;gap:1px;margin-top:3px}
.price{font-size:7px;margin-top:3px;color:var(--ink)}
.price s{color:var(--muted);margin-left:4px}

.site-footer{left:0;top:978px;width:700px;height:194px;background:var(--footer)}
.foot-col{top:998px;color:var(--footer-text)}
.foot-col h4{font-size:8px;font-weight:700;color:#fff;letter-spacing:.5px;margin-bottom:10px}
.foot-col p,.foot-col li{font-size:6.5px;line-height:1.65;color:var(--footer-text)}
.foot-col ul{list-style:none}
.foot-col li{border-bottom:1px solid #45484d;padding:2px 0}
.foot-col .news-date{color:#fff;font-weight:600}
.foot-col .read-more{color:var(--cyan);margin-top:6px}
.map{width:140px;height:78px;background:linear-gradient(135deg,#e8e6df,#d3d6d0 60%,#c8ccc6)}
.contact-row{display:flex;gap:5px;align-items:flex-start;margin-bottom:4px}
.bottom-bar{left:0;top:1172px;width:700px;height:28px;background:var(--footer-deep);color:#8d9197;font-size:6.5px;display:flex;align-items:center;justify-content:space-between;padding:0 22px}
.social{display:flex;align-items:center;gap:5px}
.social span.c{width:13px;height:13px;border-radius:50%;background:#44474c}
</style>
</head>
<body>

<header class="site-header abs">
  <div class="brand abs"><span class="brand-name">RIVERTON COMPOUNDING</span></div>
  <nav class="main-nav abs">
    <a class="active" href="#">HOME</a>
    <a href="#">ABOUT US</a>
    <a href="#">LOCATIONS</a>
    <a href="#">FORMS</a>
    <a href="#">CONTACT</a>
    <svg class="nav-search" width="10" height="10" viewBox="0 0 10 10"><circle cx="4" cy="4" r="3" fill="none" stroke="#3a3d42" stroke-width="1.2"/><line x1="6.2" y1="6.2" x2="9" y2="9" stroke="#3a3d42" stroke-width="1.2"/></svg>
  </nav>
</header>

<section class="hero abs" role="img" aria-label="Pharmacist holding a tablet in a bright pharmacy with shelves of medicines"></section>
<div class="hero-shade abs"></div>
<div class="hero-caption abs">
  <h1>COMPOUNDING PHARMACY</h1>
  <p>Our skilled pharmacists prepare medicines made to your needs, mixed fresh in our purpose built laboratory for you.</p>
</div>
<div class="hero-arrow abs" style="left:12px"><svg width="8" height="8" viewBox="0 0 8 8"><path d="M5.5 1 2.5 4l3 3" fill="none" stroke="#3a3d42" stroke-width="1.3"/></svg></div>
<div class="hero-arrow abs" style="right:12px"><svg width="8" height="8" viewBox="0 0 8 8"><path d="M2.5 1l3 3-3 3" fill="none" stroke="#3a3d42" stroke-width="1.3"/></svg></div>
<div class="hero-dots abs"><span class="on"></span><span></span><span></span></div>

<article class="tile tile-medicine abs">
  <div class="tile-art abs" role="img" aria-label="Soft photo of medicine capsules"></div>
  <h2>MEDICINE &amp; HEALTH</h2>
  <p>It is a long established fact that a reader will be distracted by the readable content of a page.</p>
</article>
<article class="tile tile-popular abs">
  <div class="tile-art abs" role="img" aria-label="Soft photo of pharmacy preparation"></div>
  <h2>CONTRARY TO POPULAR</h2>
  <p>It is a long established fact that a reader will be distracted by the readable content of a page.</p>
</article>
<article class="tile tile-care abs">
  <div class="tile-art abs" role="img" aria-label="Soft photo of pills and tablets"></div>
  <h2>CONTRARY TO POPULAR</h2>
  <p>It is a long established fact that a reader will be distracted by the readable content of a page.</p>
</article>

<section class="about abs">
  <h2 class="section-title">ABOUT COMPOUNDING PHARMACY</h2>
  <p>We make medicine to order for each patient. Our team of pharmacists has been preparing custom doses, creams and liquids for many years, working with doctors, vets and local families. Every preparation is made by hand in our purpose built laboratory, checked twice, and labelled with clear advice so you always know how to use it safely and well.</p>
  <p>When a standard product does not suit you, we can change the strength, remove an allergen, add a flavour or make a new form that is easier to take. Talk to us in store or send your doctor's script and we will explain the options and prepare your medicine quickly and with care.</p>
  <span class="btn-outline">READ MORE HERE</span>
</section>

<section class="works abs">
  <h2 class="section-title">OUR WORKS</h2>
  <p>We prepare medicines for people and pets, from gentle creams to flavoured liquids, all made fresh in our own laboratory with care.</p>
  <ul>
    <li><svg width="7" height="7" viewBox="0 0 7 7"><path d="M1 3.6l1.7 1.7L6 1.8" fill="none" stroke="#4fc3dc" stroke-width="1.3"/></svg>We do Compounding</li>
    <li><svg width="7" height="7" viewBox="0 0 7 7"><path d="M1 3.6l1.7 1.7L6 1.8" fill="none" stroke="#4fc3dc" stroke-width="1.3"/></svg>Where we are</li>
    <li><svg width="7" height="7" viewBox="0 0 7 7"><path d="M1 3.6l1.7 1.7L6 1.8" fill="none" stroke="#4fc3dc" stroke-width="1.3"/></svg>What we do there</li>
    <li><svg width="7" height="7" viewBox="0 0 7 7"><path d="M1 3.6l1.7 1.7L6 1.8" fill="none" stroke="#4fc3dc" stroke-width="1.3"/></svg>How you can order</li>
  </ul>
</section>

<section class="question abs">
  <h2>HAVE A QUESTION?</h2>
  <p>Call or visit our pharmacy and speak with a pharmacist about a medicine made for you. We are happy to help patients, doctors and vets with any request.</p>
  <span class="btn-quote abs">GET A QUOTE NOW</span>
</section>

<h2 class="section-title products abs">FEATURED PRODUCTS</h2>
<div class="product-arrows abs">
  <span><svg width="6" height="6" viewBox="0 0 6 6"><path d="M4 .8 1.8 3 4 5.2" fill="none" stroke="#8a8f96" stroke-width="1"/></svg></span>
  <span><svg width="6" height="6" viewBox="0 0 6 6"><path d="M2 .8 4.2 3 2 5.2" fill="none" stroke="#8a8f96" stroke-width="1"/></svg></span>
</div>

<article class="product abs" style="left:22px">
  <div class="product-photo" role="img" aria-label="Red capsules on white" style="background:radial-gradient(circle at 50% 55%,#d8464f 0 18%,#f4f6f8 45%)"></div>
  <h3>CONTRARY TO POPULAR</h3>
  <div class="stars"><svg width="40" height="7" viewBox="0 0 40 7"><g fill="#f5a623"><path id="s" d="M3.5 0l1 2.3 2.5.2-1.9 1.6.6 2.4-2.2-1.3-2.2 1.3.6-2.4L0 2.5l2.5-.2z"/><use href="#s" x="8"/><use href="#s" x="16"/><use href="#s" x="24"/><use href="#s" x="32"/></g></svg></div>
  <p class="price">$5.00<s>$6.00</s></p>
</article>
<article class="product abs" style="left:190px">
  <div class="product-photo" role="img" aria-label="Medicine box and blister pack" style="background:radial-gradient(ellipse at 50% 55%,#5fc7c0 0 22%,#e9f2f2 30%,#f4f6f8 55%)"></div>
  <h3>CONTRARY TO POPULAR</h3>
  <div class="stars"><svg width="40" height="7" viewBox="0 0 40 7"><g fill="#f5a623"><use href="#s"/><use href="#s" x="8"/><use href="#s" x="16"/><use href="#s" x="24"/><use href="#s" x="32"/></g></svg></div>
  <p class="price">$5.00<s>$6.00</s></p>
</article>
<article class="product abs" style="left:358px">
  <div class="product-photo" role="img" aria-label="Glass vial with blue cap" style="background:radial-gradient(ellipse at 50% 50%,#2f4fa0 0 14%,#dfe5ee 24%,#f4f6f8 50%)"></div>
  <h3>CONTRARY TO POPULAR</h3>
  <div class="stars"><svg width="40" height="7" viewBox="0 0 40 7"><g fill="#f5a623"><use href="#s"/><use href="#s" x="8"/><use href="#s" x="16"/><use href="#s" x="24"/><use href="#s" x="32"/></g></svg></div>
  <p class="price">$5.00<s>$6.00</s></p>
</article>
<article class="product abs" style="left:526px">
  <div class="product-photo" role="img" aria-label="Golden gel capsules" style="background:radial-gradient(circle at 50% 55%,#f0c23a 0 20%,#f8eecb 32%,#f4f6f8 55%)"></div>
  <h3>CONTRARY TO POPULAR</h3>
  <div class="stars"><svg width="40" height="7" viewBox="0 0 40 7"><g fill="#f5a623"><use href="#s"/><use href="#s" x="8"/><use href="#s" x="16"/><use href="#s" x="24"/><use href="#s" x="32"/></g></svg></div>
  <p class="price">$5.00<s>$6.00</s></p>
</article>

<footer class="site-footer abs"></footer>
<div class="foot-col abs" style="left:22px;width:150px">
  <h4>PHARMACY NEWS</h4>
  <p class="news-date">Posted on March 10, 2015</p>
  <p>New flavoured liquid medicines for children and pets are now prepared daily in our laboratory. Ask us in store.</p>
  <p class="read-more">Read more &rsaquo;</p>
</div>
<div class="foot-col abs" style="left:210px;width:110px">
  <h4>WELCOME</h4>
  <ul><li>Home</li><li>About us</li><li>Locations</li><li>Forms</li><li>Contact</li></ul>
</div>
<div class="foot-col abs" style="left:355px;width:150px">
  <h4>LOCATIONS</h4>
  <div class="map" role="img" aria-label="Street map showing the pharmacy location"></div>
</div>
<div class="foot-col abs" style="left:545px;width:135px">
  <h4>CONTACT INFO</h4>
  <div class="contact-row"><svg width="7" height="9" viewBox="0 0 7 9"><path d="M3.5 0A3.3 3.3 0 0 0 .2 3.3C.2 5.7 3.5 9 3.5 9s3.3-3.3 3.3-5.7A3.3 3.3 0 0 0 3.5 0z" fill="#4fc3dc"/><circle cx="3.5" cy="3.3" r="1.2" fill="#2e3034"/></svg><p>14 Harbour Lane, Riverton<br>Open Mon to Sat, 8am to 6pm</p></div>
  <div class="contact-row"><svg width="7" height="7" viewBox="0 0 7 7"><path d="M1.5 0 3 1.8 2 2.8a4.5 4.5 0 0 0 2.2 2.2l1-1L7 5.5 5.8 7C2.8 6.8.2 4.2 0 1.2z" fill="#4fc3dc"/></svg><p>1200 555 0148</p></div>
  <div class="contact-row"><svg width="8" height="6" viewBox="0 0 8 6"><rect x=".4" y=".4" width="7.2" height="5.2" fill="none" stroke="#4fc3dc" stroke-width=".8"/><path d="M.5.6 4 3.3 7.5.6" fill="none" stroke="#4fc3dc" stroke-width=".8"/></svg><p>hello@compoundrx.example</p></div>
</div>

<div class="bottom-bar abs">
  <span>&copy; 2015 Riverton Compounding. All rights reserved.</span>
  <span class="social">Connect with our social network <span class="c"></span><span class="c"></span><span class="c"></span></span>
</div>

</body>
</html>
```